Webdesign für neue Weinmarke
Zielgruppe
Kelchwandler ist eine neue Weinmarke. Es wird vorerst drei grundlegende Sorten geben: einen Rotwein, einen Weißwein und einen Rosé. Für diese neue Weinmarke wollen wir eine Webseite gestalten, welche die Weine ansprechend darstellt und zusätzlich den Kunden die Möglichkeit gibt, mehr Informationen über den Wein einzuholen. Die Marke Kelchwandler ist auch im Etikett an den Graf von Tressenbach angelehnt. Das Etikett zeigt den Baron, wie er auf einem Weinfass reitet – daher der Name „Kelchwandler“. Die Story, die wir mit dem Wein spielen, ist, dass die besonderen Fähigkeiten des Barons auch auf den Genuss des Kelchwandler zurückzuführen sind.
Die Zielgruppe für den Kelchwandler ist breit gefächert und schließt per se erst mal keine Personengruppe aus. Der Wein soll eher im niedrigeren Preissegment verkauft werden.
Aufgabenstellung
Es soll eine neue Webseite designt werden, die sich im Aufbau an der die Webseite http://www.velgor-example.de/#!/de/unsere-weine/sortiment orientieren kann. Zudem können für die Entwicklung kleine Animationen berücksichtigt werden, die die Seite auflockern. Das Design soll eine responsive Webseite unterstützen. Das Design soll zur Weinmarke Kelchwandler passen von der wir bisher nur das Etikett haben.

```html
<!DOCTYPE html>
<html lang="de">
<head>
<meta charset="utf-8">
<title>Kelchwandler – Willkommen</title>
<link rel="stylesheet" href="https://fonts.googleapis.com/css2?family=Oswald:wght@300;400&family=Mukta:wght@300;400&display=swap">
<style>
  :root {
    --paper: #f9f8f6;
    --ink: #231f20;
    --wine: #3d1c27;
    --on-wine: #f4eef0;
    --footer: #dcdcdc;
    --rule: #2b2526;
    --head: "Oswald", "Arial Narrow", sans-serif;
    --body: "Mukta", "Helvetica Neue", sans-serif;
  }
  * { margin: 0; padding: 0; box-sizing: border-box; }
  html, body { width: 1018px; height: 1200px; overflow: hidden; background: var(--paper); }
  body { position: relative; color: var(--ink); font-family: var(--body); font-weight: 300; }

  .main-nav { position: absolute; left: 33px; top: 6px; list-style: none; }
  .main-nav li { font-family: var(--head); font-weight: 400; font-size: 8.2px; line-height: 13.2px; letter-spacing: -0.1px; }
  .main-nav .active { position: relative; }
  .main-nav .active::before { content: ""; position: absolute; left: -32px; top: 6.5px; width: 27px; height: 1px; background: var(--ink); }
  .meta-nav { position: absolute; right: 11px; top: 6px; list-style: none; text-align: right; }
  .meta-nav li { font-family: var(--head); font-size: 7.2px; line-height: 13.2px; }

  .brand { position: absolute; left: 449px; top: 8px; width: 120px; text-align: center; }
  .brand-visual { display: block; width: 90px; height: 82px; margin: 0 auto; background: radial-gradient(ellipse at center, #8d8a89 0%, #c9c6c4 55%, var(--paper) 75%); }
  .brand-name { font-family: var(--head); font-weight: 400; font-size: 12px; letter-spacing: 0.5px; margin-top: 2px; }

  .divider { position: absolute; left: 430px; width: 159px; height: 2px; background: var(--rule); }

  .intro { position: absolute; left: 299px; top: 210px; width: 420px; text-align: center; }
  .intro h1 { font-family: var(--head); font-weight: 300; font-size: 13.2px; line-height: 20px; white-space: nowrap; }
  .intro p { font-size: 9.3px; line-height: 11.6px; margin: 9px auto 0; width: 400px; }

  .section-title { position: absolute; left: 0; width: 1018px; text-align: center; font-family: var(--head); font-weight: 300; font-size: 15px; }

  .product-band { position: absolute; left: 0; top: 425px; width: 1018px; height: 210px; }
  .bottle { position: absolute; left: 218px; top: 429px; width: 45px; height: 195px; border-radius: 14px 14px 6px 6px; background: linear-gradient(90deg, #1c1114, #3a2228 45%, #1c1114); }
  .product { position: absolute; left: 281px; top: 462px; width: 522px; color: var(--on-wine); }
  .product h2 { font-family: var(--head); font-weight: 300; font-size: 13px; line-height: 17px; }
  .product h3 { font-family: var(--head); font-weight: 300; font-size: 9px; line-height: 12px; }
  .product .mini-rule { width: 57px; height: 1px; background: var(--on-wine); margin: 6px 0 6px; }
  .product .lead { font-size: 8.4px; line-height: 11.6px; }
  .region-map { position: absolute; left: 281px; top: 543px; width: 35px; height: 46px; background: var(--on-wine); border-radius: 40% 45% 35% 40%; }
  .region-text { position: absolute; left: 323px; top: 543px; width: 362px; font-size: 8.4px; line-height: 11.6px; color: var(--on-wine); }
  .btn { position: absolute; display: flex; align-items: center; justify-content: center; gap: 8px; border-radius: 10px; font-family: var(--body); font-weight: 300; font-size: 9.5px; }
  .btn::after { content: "›"; font-weight: 400; }
  .btn-light { left: 736px; top: 559px; width: 64px; height: 18px; border: 1.2px solid var(--on-wine); color: var(--on-wine); }
  .btn-dark { left: 448px; top: 1001px; width: 122px; height: 19px; border: 1.2px solid var(--ink); color: var(--ink); }

  .slider-dots { position: absolute; right: 9px; top: 505px; list-style: none; text-align: right; color: var(--on-wine); }
  .slider-dots li { height: 16px; font-family: var(--head); font-weight: 300; font-size: 7.2px; line-height: 10px; display: flex; justify-content: flex-end; align-items: center; gap: 6px; }
  .slider-dots li::after { content: ""; width: 6px; height: 6px; border: 1.2px solid var(--on-wine); border-radius: 50%; }

  .story { position: absolute; left: 306px; top: 776px; width: 406px; text-align: center; }
  .story h3 { font-family: var(--head); font-weight: 400; font-size: 9.5px; line-height: 12px; }
  .story p { font-size: 9.3px; line-height: 11.65px; }

  .site-footer { position: absolute; left: 0; top: 1128px; width: 1018px; height: 72px; }
  .footer-copy { position: absolute; left: 218px; top: 1169px; font-size: 8.6px; }
  .footer-links { position: absolute; left: 700px; top: 1169px; display: flex; font-size: 8.6px; list-style: none; }
  .footer-links li + li { border-left: 1px solid #999; margin-left: 5px; padding-left: 5px; }
</style>
</head>
<body>

<ul class="main-nav">
  <li class="active">Willkommen</li>
  <li>Kelchwandler Rotwein</li>
  <li>Kelchwandler Rosé</li>
  <li>Kelchwandler Weißwein</li>
</ul>
<ul class="meta-nav">
  <li>Kontakt</li>
  <li>Impressum</li>
</ul>

<header class="brand">
  <span class="brand-visual" role="img" aria-label="Radierung: Reiter auf einem Weinfass"></span>
  <div class="brand-name">KELCHWANDLER</div>
</header>

<div class="divider" style="top:155px" role="img" aria-label="Zierornament"></div>

<section class="intro">
  <h1>Kelchwandler – Der Wein, der schon dem Grafen selbst Anmut und Heldengeist verlieh.</h1>
  <p>Genießen Sie Kelchwandler als gehaltvollen und fruchtbetonten Rotwein, als lieblichen und fruchtigen Rosé oder als feinherben Riesling. Die drei Weine überzeugen durch höchste Qualität, harmonische Säuren und ein außergewöhnliches Design.</p>
</section>

<div class="divider" style="top:330px" role="img" aria-label="Zierornament"></div>

<h2 class="section-title" style="top:384px">Unser Produktsortiment</h2>

<svg class="product-band" viewBox="0 0 1018 210" aria-hidden="true">
  <path d="M0 19 H455 C480 19 495 14 509 14 C523 14 538 19 563 19 H1018 V182 H563 C538 182 523 187 509 187 C495 187 480 182 455 182 H0 Z" fill="var(--wine)"/>
  <path d="M509 0 C506 6 503 9 503 12 A6 6 0 0 0 515 12 C515 9 512 6 509 0 Z" fill="var(--wine)"/>
  <path d="M506 13 L509 10 L512 13" stroke="var(--paper)" stroke-width="1" fill="none"/>
  <path d="M509 195 C506 201 503 204 503 207 A6 6 0 0 0 515 207 C515 204 512 201 509 195 Z" fill="var(--wine)" transform="translate(0,-4)"/>
  <path d="M506 201 L509 204 L512 201" stroke="var(--paper)" stroke-width="1" fill="none"/>
</svg>

<div class="bottle" role="img" aria-label="Flasche Kelchwandler Dornfelder halbtrocken"></div>

<article class="product">
  <h2>Kelchwandler Rotwein</h2>
  <h3>Kelchwandler Pfälzer Dornfelder</h3>
  <div class="mini-rule"></div>
  <p class="lead">Muster Kurze Beschreibung Lorem ipsum dolor sit amet, consetetur sadipscing elitr, sed diam nonumy eirmod tempor invidunt vero eos et accusam et justo labore et dolore magna aliquyam erat, sed diam voluptua. At vero takimata sanctus esteos et accusam et justo duo dolores et ea rebum.</p>
</article>
<div class="region-map" role="img" aria-label="Deutschlandkarte mit Markierung der Pfalz"></div>
<p class="region-text">Des Kelchwandlers Rot- sowie Weißwein kommen aus dem zweitgrößten deutschen Weinanbaugebiet, der Pfalz. Das einzigartige Klima dieser Region bringt gehaltvolle und wertige Weine hervor. Die Pfalz ist Deutschlands größtes Rotweingebiet und beheimatet zudem auch des Kelchwandlers feinherben Riesling.</p>
<a class="btn btn-light">Details</a>

<ul class="slider-dots">
  <li>Kelchwandler Rotwein</li>
  <li></li>
  <li></li>
</ul>

<div class="divider" style="top:689px" role="img" aria-label="Zierornament"></div>

<h2 class="section-title" style="top:743px">Graf von Tressenbach</h2>

<section class="story">
  <h3>1. Ritt auf dem Weinfass</h3>
  <p>Es war im Herbst, meine Damen und Herren, als wir auf unserem Gut in der Pfalz die Lese feierten und der Kellermeister ein neues Fass aus dem Gewölbe rollen ließ. Kaum hatte das Fass die oberste Stufe erreicht, da sprang der Spund heraus, und der Duft des jungen Dornfelders zog über den ganzen Hof. Die Knechte wollten es festhalten, doch das Fass kam ins Rollen und polterte den Weinberg hinab, geradewegs auf den Fluss zu. Ich zögerte nicht lange, nahm einen kräftigen Anlauf, schwang mich hinauf und hielt mich an den eisernen Reifen fest wie an den Zügeln eines edlen Rosses. Über Stock und Stein ging der Ritt, zwischen den Rebzeilen hindurch, vorbei an staunenden Winzerinnen, die vor Schreck ihre Körbe fallen ließen. Am Ufer angekommen, lenkte ich mein hölzernes Ross mit einem geschickten Druck der Fersen über einen schmalen Steg, und so trabten wir trockenen Fußes bis ins nächste Dorf, wo gerade das Weinfest begann. Dort empfing man mich mit Musik und Jubel, und das Fass, das auf dem ganzen Weg keinen einzigen Tropfen verloren hatte, wurde unter großem Beifall angestochen. Seit jenem Tage nennt man mich im ganzen Land den Kelchwandler, und ich versichere Ihnen: Ein Glas dieses Weines verleiht jedem Reiter Mut, Geschick und einen sicheren Sitz.</p>
</section>
<a class="btn btn-dark">Weitere Geschichten</a>

<div class="divider" style="top:1079px" role="img" aria-label="Zierornament"></div>

<svg class="site-footer" viewBox="0 0 1018 72" aria-hidden="true">
  <path d="M0 6 H480 C495 6 500 2 509 2 C518 2 523 6 538 6 H1018 V72 H0 Z" fill="var(--footer)"/>
</svg>
<p class="footer-copy">© Kelchwandler 2018. Alle rechte vorbehalten.</p>
<ul class="footer-links">
  <li>Impressum</li>
  <li>Datenschutz</li>
</ul>

</body>
</html>
```